Vantro cards

I am in the auto motive, transportation business I would like a business card that is Something cool, modern edgy, having to do with car culture. I offer towing service for high and exotic cars. I also provide towing for collisions and car accidents. I offer open and enclosed transport nationwide.

Target Market(s)

Car culture people high end auto collectors

Industry/Entity Type

Towing car carrier

Contact Information for Business Card

My company colors black yellow and silver

Font styles to use
Serif

```html
<!DOCTYPE html>
<html lang="en">
<head>
<meta charset="utf-8">
<title>Vantro Transportation – Business Cards</title>
<link rel="stylesheet" href="https://fonts.googleapis.com/css2?family=Montserrat:wght@400;600;700;800&display=swap">
<style>
  :root {
    --yellow: #f7dc4a;
    --black: #000000;
    --charcoal: #1c1c1c;
    --charcoal-light: #2a2a2a;
    --white: #ffffff;
    --silver: #e6e6e6;
    --stage: #d9d6d0;
  }
  * { box-sizing: border-box; margin: 0; padding: 0; }
  html, body {
    width: 900px; height: 1200px; overflow: hidden;
    background: var(--stage);
    font-family: "Montserrat", sans-serif;
  }
  .canvas { position: relative; width: 900px; height: 1200px; }

  .card {
    position: absolute; left: 80px; width: 742px; height: 442px;
    border-radius: 30px; overflow: hidden;
    box-shadow: 0 6px 14px rgba(0,0,0,0.35);
  }
  .card--front { top: 130px; display: flex; }
  .card--back { top: 638px; background: linear-gradient(135deg, var(--charcoal) 0%, var(--charcoal) 55%, var(--charcoal-light) 100%); }

  .front__brand {
    width: 371px; background: var(--white);
    display: flex; align-items: center; justify-content: center;
  }
  .front__info {
    position: relative; flex: 1; background: var(--black);
    color: var(--silver); padding: 106px 0 0 36px;
  }
  .front__info::before {
    content: ""; position: absolute; left: 0; top: 188px;
    width: 6px; height: 72px; background: var(--yellow);
  }

  .brand-name {
    font-weight: 800; color: var(--black); text-transform: uppercase;
    text-align: center; line-height: 1.1; letter-spacing: 1px;
  }
  .brand-name--front { font-size: 46px; }
  .brand-name--front small { display: block; font-size: 19px; letter-spacing: 2px; }
  .brand-name--back { color: var(--yellow); font-size: 56px; }
  .brand-name--back small { display: block; font-size: 23px; letter-spacing: 3px; }

  .person__name { color: var(--yellow); font-size: 26px; font-weight: 600; }
  .person__role { font-size: 16px; margin-top: 4px; }

  .contact { list-style: none; margin-top: 30px; font-size: 16px; }
  .contact li { display: flex; align-items: center; gap: 10px; height: 21px; }
  .contact svg { width: 15px; height: 13px; fill: var(--yellow); flex: none; }

  .address { margin-top: 22px; font-size: 16px; line-height: 20px; }

  .back__truck {
    position: absolute; right: 0; top: 40px; width: 330px; height: 360px;
    border-radius: 120px 0 0 90px;
    background: linear-gradient(120deg, rgba(60,60,60,0) 0%, #3a3a3a 45%, #6b6b6b 100%);
  }
  .back__brand {
    position: absolute; left: 0; right: 0; top: 150px;
    display: flex; justify-content: center;
  }
  .back__stripe {
    position: absolute; left: 0; right: 0; bottom: 0; height: 12px;
    background: var(--yellow);
  }
</style>
</head>
<body>
<main class="canvas">
  <section class="card card--front">
    <div class="front__brand">
      <p class="brand-name brand-name--front">Vantro<small>Transportation</small></p>
    </div>
    <div class="front__info">
      <h1 class="person__name">Dana Reyes</h1>
      <p class="person__role">Owner</p>
      <ul class="contact">
        <li><svg viewBox="0 0 16 14" aria-hidden="true"><path d="M1 4c0-2 3-3 7-3s7 1 7 3v1h-4V4H5v1H1zM3 7h10l1 6H2z"/></svg>(555) 014-2290</li>
        <li><svg viewBox="0 0 16 14" aria-hidden="true"><path d="M1 2h14v1L8 8 1 3zM1 5l7 5 7-5v7H1z"/></svg>info@vantrotransportation.com</li>
        <li><svg viewBox="0 0 16 16" aria-hidden="true"><circle cx="8" cy="8" r="7"/></svg>www.vantrotransportation.com</li>
      </ul>
      <p class="address">48 Harbor Lane<br>Millbrook, PA 17000</p>
    </div>
  </section>

  <section class="card card--back">
    <div class="back__truck" role="img" aria-label="Large dark silhouette of a flatbed tow truck cab"></div>
    <div class="back__brand">
      <p class="brand-name brand-name--back">Vantro<small>Transportation</small></p>
    </div>
    <div class="back__stripe"></div>
  </section>
</main>
</body>
</html>
```